Hardcore nerd needs to stand out in a sea of dull Defence business cards

Wombarra Devices is a new Australian consulting engineering company that turns research and theory into practical systems. No evangelistic fluff, just mathematics and physics into electronic and optical circuits for consumer products, scientific research or Defence applications.

We already have a recognised logo (provided) which is often dark blue/black on a light background but we're open to other combinations. (Us engineers tend to have limited aesthetic imagination :)

Some of our recent products have included:
* Instrumentation for electrical testing,
* Radar jammers,
* GPS antenna design,
* Satellite tracking systems,
* High power lasers

We're open to both single and double-sided designs - happy to be convinced either way.

P.S. Another group is working on the web page, so - alas - our web site is currently of no use for images/ideas...

Target Market(s)

Engineering managers,
Scientists

Contact Information for Business Card

Dr Colin Harte
R&D Engineer

colin@wombarradevices.com.au
0427 563 710

PO Box XXX (to be confirmed)
Kelsby ACT 2917
Australia

Font styles to use
Serif
Sans Serif

Colors

Designer to choose colors to be used in the design.

Requirements
Must have
• My contact details!
• I've had many (great) "bold and plain" designs submitted already, so feel free to be artistically creative :)
• Happy to take advice re fonts/colours/printability etc.
Nice to have
• I'm not sure if "lists" are more at home on a CV than a business card, but representative services include:
• Applied electromagnetics
• RF and high speed electronics
• Signal and image processing
• Electro-optical and laser systems
• Concept-to-prototype design services
• If you're considering double sided cards, then often measuring/alignment grids/rulers feature on the back of similar cards.
• e.g. https://www.veltranoptics.example/newgrouppage9.cfm?objectgroup_id=4183
• https://www.veltranoptics.example/newgrouppage9.cfm?objectgroup_ID=4185
• ..or even a "Smith chart" (google will return lots)
• Generic images to represent a capability might work - googling images associated with keyword for each of these areas might help:
• - "passive radar", "phased array", "fdtd", "vircator"
• RF and high speed electronic design
• - "smith chart", "microstrip circuits", "dimensioned drawing", "electronic schematic"
• - "dft", "iir filter"
• - "optical cavity". "laser energy level diagram"
• Background/watermarked images outlines/wireframes/schematics would probably look OK.
Should not have
• If a list of projects/services is provided, it is important not to make the client feel that this is "all" the company can do. Engineering design is a creative discipline (like graphics :)
• Please, no stock "military" snaps like planes, missiles, etc!

```html
<!DOCTYPE html>
<html lang="en">
<head>
<meta charset="utf-8">
<title>Wombarra Devices — Business Card</title>
<link rel="stylesheet" href="https://fonts.googleapis.com/css2?family=Arimo:wght@400;700&display=swap">
<style>
  :root {
    --stage: #000000;
    --steel-light: #c9c9c9;
    --steel-mid: #a9a9a9;
    --steel-dark: #8d8d8d;
    --panel-light: #ececec;
    --panel-mid: #d4d4d4;
    --navy: #0c2462;
    --name-blue: #17337a;
    --text-dark: #111111;
    --text-grey: #4a4a4a;
    --mark-black: #111111;
    --part-dark: #3a3a3a;
    --part-mid: #5c5c5c;
  }
  * { margin: 0; padding: 0; box-sizing: border-box; }
  html, body {
    width: 1067px; height: 1200px; overflow: hidden;
    background: var(--stage);
    font-family: "Arimo", Arial, sans-serif;
  }
  .card {
    position: absolute; left: 67px; width: 933px; height: 533px; overflow: hidden;
    background:
      repeating-linear-gradient(180deg, rgba(255,255,255,0.10) 0 1px, rgba(0,0,0,0.05) 1px 2px, rgba(255,255,255,0) 2px 3px),
      linear-gradient(100deg, var(--steel-dark), var(--steel-light) 45%, var(--steel-mid) 75%, var(--steel-light));
  }
  .card--front { top: 53px; }
  .card--back { top: 632px; }
  .card svg { position: absolute; inset: 0; width: 933px; height: 533px; }
  .brand-name { font-family: "Arimo", Arial, sans-serif; font-weight: 700; fill: var(--mark-black); }
  .contact { position: absolute; left: 486px; color: var(--text-dark); }
  .contact__name { position: absolute; top: 136px; font-size: 32px; font-weight: 700; color: var(--name-blue); letter-spacing: -0.5px; white-space: nowrap; }
  .contact__role { position: absolute; top: 178px; font-size: 20px; color: var(--text-grey); white-space: nowrap; letter-spacing: 0.5px; }
  .contact__address { position: absolute; top: 236px; font-size: 21px; line-height: 29px; white-space: nowrap; letter-spacing: 0.4px; }
  .contact__list { position: absolute; top: 311px; list-style: none; font-size: 21px; line-height: 29px; letter-spacing: 0.4px; }
  .contact__list li { display: flex; align-items: center; white-space: nowrap; }
  .contact__list svg { position: static; width: 17px; height: 17px; margin: 0 17px 0 9px; }
</style>
</head>
<body>

<section class="card card--front">
  <svg viewBox="0 0 933 533" aria-hidden="false">
    <defs>
      <linearGradient id="panelGrad" x1="0" y1="0" x2="1" y2="0">
        <stop offset="0" stop-color="#f4f4f4"/>
        <stop offset="1" stop-color="#cfcfcf"/>
      </linearGradient>
      <linearGradient id="partGrad" x1="0" y1="0" x2="1" y2="1">
        <stop offset="0" stop-color="#6a6a6a"/>
        <stop offset="1" stop-color="#3a3a3a"/>
      </linearGradient>
    </defs>
    <path class="info-panel" d="M520 0 Q410 240 470 484 L933 484 L933 0 Z" fill="url(#panelGrad)" opacity="0.85"/>
    <path class="panel-edge" d="M520 0 Q410 240 470 484" fill="none" stroke="#333" stroke-width="5"/>
    <polygon class="accent-band" points="400,533 449,484 933,484 933,533" fill="var(--navy)"/>
    <line x1="449" y1="484" x2="933" y2="484" stroke="#6a7fb0" stroke-width="1.5"/>

    <ellipse role="img" aria-label="Photo of a small aperture alignment disk" cx="158" cy="124" rx="38" ry="40" fill="url(#partGrad)" opacity="0.55"/>
    <rect role="img" aria-label="Photo of a tee-shaped alignment target plate" x="253" y="46" width="165" height="163" rx="14" fill="url(#partGrad)" opacity="0.55"/>
    <ellipse role="img" aria-label="Photo of a cylindrical lens-mount alignment target" cx="196" cy="418" rx="56" ry="58" fill="url(#partGrad)" opacity="0.55"/>
    <ellipse role="img" aria-label="Photo of a crosshair alignment disk" cx="383" cy="444" rx="34" ry="54" fill="url(#partGrad)" opacity="0.55"/>

    <circle cx="136" cy="263" r="46" fill="var(--mark-black)"/>
    <text class="brand-name" x="198" y="258" font-size="36">WOMBARRA</text>
    <text class="brand-name" x="198" y="294" font-size="24" letter-spacing="6">DEVICES</text>
  </svg>

  <div class="contact">
    <div class="contact__name">Dr Colin Harte</div>
    <div class="contact__role">R&amp;D Engineer</div>
    <div class="contact__address">PO Box XXX Kelsby ACT 2917<br>Australia</div>
    <ul class="contact__list">
      <li>
        <svg viewBox="0 0 20 20"><circle cx="10" cy="10" r="9.5" fill="var(--navy)"/><path d="M6 5 q-1 5 4 9 q4 3 5 1 l-2-2 l-1.5 1 q-3-2-4-4.5 l1-1.5 Z" fill="#fff"/></svg>
        0427 563 710
      </li>
      <li>
        <svg viewBox="0 0 20 20"><rect x="1" y="4" width="18" height="13" rx="1.5" fill="var(--navy)"/><path d="M2 5 L10 11 L18 5" fill="none" stroke="#fff" stroke-width="1.5"/></svg>
        colin@wombarradevices.com.au
      </li>
      <li>
        <svg viewBox="0 0 20 20"><circle cx="10" cy="10" r="9" fill="var(--navy)"/><g fill="none" stroke="#fff" stroke-width="1.2"><ellipse cx="10" cy="10" rx="4" ry="8"/><line x1="2" y1="10" x2="18" y2="10"/><line x1="3.5" y1="6" x2="16.5" y2="6"/><line x1="3.5" y1="14" x2="16.5" y2="14"/></g></svg>
        www.veltranoptics.example
      </li>
    </ul>
  </div>
</section>

<section class="card card--back">
  <svg viewBox="0 0 933 533">
    <defs>
      <linearGradient id="partGrad2" x1="0" y1="0" x2="1" y2="1">
        <stop offset="0" stop-color="#5a5a5a"/>
        <stop offset="1" stop-color="#262626"/>
      </linearGradient>
    </defs>
    <rect role="img" aria-label="Photo of a tee-shaped alignment target plate" x="40" y="44" width="211" height="222" rx="16" fill="url(#partGrad2)"/>
    <ellipse role="img" aria-label="Photo of a cylindrical lens-mount alignment target" cx="187" cy="375" rx="71" ry="73" fill="url(#partGrad2)"/>
    <ellipse role="img" aria-label="Photo of a small aperture alignment disk" cx="408" cy="430" rx="33" ry="36" fill="url(#partGrad2)"/>
    <ellipse role="img" aria-label="Photo of a crosshair alignment disk" cx="600" cy="421" rx="44" ry="71" fill="url(#partGrad2)"/>

    <circle cx="431" cy="186" r="86" fill="var(--mark-black)"/>
    <text class="brand-name" x="535" y="194" font-size="56">WOMBARRA</text>
    <text class="brand-name" x="537" y="250" font-size="38" letter-spacing="7">DEVICES</text>
  </svg>
</section>

</body>
</html>
```